MV Decor

There is a sample provided with the arabic text of the business card. please copy paste the same text and the same Logo (The two triangles) Just try to incorproate the Brown background attached (you are free to change the colors) Id like the colors to be mainly shades of black and red.

```html
<!DOCTYPE html>
<html lang="ar">
<head>
<meta charset="utf-8">
<title>MV Decor — Business Card</title>
<link rel="stylesheet" href="https://fonts.googleapis.com/css2?family=Cairo:wght@300;400;700&family=Aref+Ruqaa:wght@400;700&family=Roboto:wght@400&display=swap">
<style>
  :root {
    --page-bg: #1d1819;
    --card-red: #cb2143;
    --card-red-light: #dc3555;
    --card-red-deep: #b81a3a;
    --ink-white: #ffffff;
    --ink-black: #231f20;
  }
  * { margin: 0; padding: 0; box-sizing: border-box; }
  html, body {
    width: 1125px; height: 1200px; overflow: hidden;
    background: var(--page-bg);
  }
  .canvas { position: relative; width: 1125px; height: 1200px; }

  .card {
    position: absolute; left: 170px; width: 826px; height: 472px;
    overflow: hidden; color: var(--ink-white);
  }
  .card--front { top: 106px; }
  .card--back { top: 638px; }

  .card__texture {
    position: absolute; inset: 0;
    background:
      radial-gradient(ellipse at 72% 35%, var(--card-red-light) 0%, transparent 60%),
      linear-gradient(160deg, var(--card-red) 0%, var(--card-red-deep) 100%);
  }

  .brand-name {
    font-family: "Cairo", sans-serif; font-weight: 700;
    text-transform: uppercase; letter-spacing: 1px;
    color: var(--ink-white); line-height: 1;
  }

  /* front */
  .front__brand { position: absolute; left: 66px; top: 64px; font-size: 50px; }
  .front__identity {
    position: absolute; right: 530px; top: 150px; direction: rtl; text-align: right;
    font-family: "Aref Ruqaa", serif;
  }
  .front__name { font-size: 27px; font-weight: 700; line-height: 1.4; }
  .front__title { font-size: 18px; text-align: center; margin-top: -4px; }
  .front__credentials {
    position: absolute; right: 356px; top: 240px; direction: rtl; text-align: right;
    list-style: none; font-family: "Cairo", sans-serif; font-weight: 400;
    font-size: 20px; line-height: 27px; letter-spacing: .5px;
  }
  .front__phone {
    position: absolute; left: 64px; top: 378px; display: flex; align-items: center; gap: 8px;
    font-family: "Roboto", sans-serif; font-size: 21px;
  }
  .front__phone svg { width: 20px; height: 20px; }
  .front__mark {
    position: absolute; left: 620px; top: 300px; width: 150px;
    display: flex; flex-direction: column; align-items: center; gap: 12px;
  }
  .mark-square { width: 42px; height: 42px; background: var(--ink-black); }
  .front__mark .brand-name { font-size: 26px; }

  /* back */
  .back__mark {
    position: absolute; left: 130px; top: 150px; width: 210px;
    display: flex; flex-direction: column; align-items: center; gap: 20px;
  }
  .back__mark .mark-square { width: 70px; height: 70px; }
  .back__mark .brand-name { font-size: 44px; }
  .back__credentials {
    position: absolute; left: 385px; width: 320px; top: 100px;
    list-style: none; direction: rtl;
    font-family: "Cairo", sans-serif; font-weight: 400;
    font-size: 24px; line-height: 33px; letter-spacing: .6px;
  }
  .back__credentials li { position: relative; text-align: right; padding-left: 22px; }
  .back__credentials li::before {
    content: ""; position: absolute; left: 2px; top: 14px;
    width: 9px; height: 9px; border-radius: 50%; background: var(--ink-white);
  }
</style>
</head>
<body>
<main class="canvas">

  <section class="card card--front">
    <div class="card__texture" role="img" aria-label="Red background with a soft grid pattern of small squares and circles"></div>
    <div class="brand-name front__brand">MV Decor</div>
    <div class="front__identity">
      <p class="front__name">المهندس / سامي خالد النوري</p>
      <p class="front__title">استاذ جامعي</p>
    </div>
    <ul class="front__credentials">
      <li>ماجستير هندسة ديكور</li>
      <li>دبلوم عالي فن تشكيلي</li>
      <li>جامعة الأفق (باريس)</li>
      <li>استشارات هندسية - فنية</li>
    </ul>
    <p class="front__phone">
      <svg viewBox="0 0 24 24" aria-hidden="true"><path fill="#fff" d="M6.6 10.8a15.1 15.1 0 0 0 6.6 6.6l2.2-2.2a1 1 0 0 1 1-.25 11.4 11.4 0 0 0 3.6.57 1 1 0 0 1 1 1V20a1 1 0 0 1-1 1A17 17 0 0 1 3 4a1 1 0 0 1 1-1h3.5a1 1 0 0 1 1 1c0 1.25.2 2.45.57 3.57a1 1 0 0 1-.25 1z"/></svg>
      <span>35550142 / 66550198</span>
    </p>
    <div class="front__mark">
      <span class="mark-square" aria-hidden="true"></span>
      <span class="brand-name">MV Decor</span>
    </div>
  </section>

  <section class="card card--back">
    <div class="card__texture" role="img" aria-label="Red background with a soft grid pattern of small squares and circles"></div>
    <div class="back__mark">
      <span class="mark-square" aria-hidden="true"></span>
      <span class="brand-name">MV Decor</span>
    </div>
    <ul class="back__credentials">
      <li>ماجستير هندسة ديكور</li>
      <li>دبلوم عالي فن تشكيلي</li>
      <li>جامعة الأفق (باريس)</li>
      <li>استشارات هندسية - فنية</li>
      <li>ماجستير هندسة ديكور</li>
      <li>دبلوم عالي فن تشكيلي</li>
      <li>جامعة الأفق (باريس)</li>
      <li>استشارات هندسية - فنية</li>
    </ul>
  </section>

</main>
</body>
</html>
```